One Page Website for Personal Trainer in London

I have a logo and need a one page website designed around my branding. I am a freelance Personal Trainer based in London specialising in bodyweight training for men and women. I would like the site to be modern and clean but not overtly urban in design.
I need the following headings:
About Me
My Services
Events
Blog
I don't need them to be seperate pages but if they can link to further down the page that would be great.
Industry/Entity Type
Personal Trainer
Coding
Coded - Design and coding required
Number of Pages Required
1 page
Requirements
Must have
- I need the following headings:
- About Me
- My Services
- Events
- Blog
- mobile friendly formatting
- health and fitness related photography
- Colour scheme in keeping with my existing logo

```html
<!DOCTYPE html>
<html lang="en">
<head>
<meta charset="utf-8">
<title>Marlowe Finch – Personal Training</title>
<link href="https://fonts.googleapis.com/css2?family=Nunito:wght@400;600;700&family=Open+Sans:wght@400;600&display=swap" rel="stylesheet">
<style>
:root{
  --orange:#f7941d;
  --ink:#222222;
  --text:#555555;
  --muted:#777777;
  --white:#ffffff;
  --light:#f2f2f2;
  --footer:#2a2a2a;
  --dark:#1c1c1c;
}
*{box-sizing:border-box;margin:0;padding:0}
html,body{width:1200px;height:3209px;overflow:hidden}
body{position:relative;font-family:'Open Sans',Arial,sans-serif;color:var(--text);background:var(--white)}
a{color:inherit;text-decoration:none}

/* header */
.site-header{position:absolute;left:0;top:0;width:1200px;height:165px;background:var(--white);border-top:6px solid var(--orange)}
.brand{position:absolute;left:66px;top:96px;width:220px;text-align:center;white-space:nowrap;font-family:'Nunito',sans-serif;font-weight:700;font-size:24px;color:var(--orange);line-height:1}
.brand-sub{position:absolute;left:66px;top:126px;width:220px;text-align:center;white-space:nowrap;font-family:'Nunito',sans-serif;font-size:9px;letter-spacing:3px;color:var(--ink);line-height:1}
.brand-dot{position:absolute;left:152px;top:22px;width:46px;height:46px;border-radius:50%;background:var(--orange)}
.header-phone{position:absolute;left:678px;top:48px;display:flex;align-items:center;gap:8px;font-family:'Nunito',sans-serif;font-size:22px;color:var(--ink);white-space:nowrap}
.social{position:absolute;display:flex;gap:10px}
.social span{width:22px;height:22px;border-radius:3px}
.header-social{left:866px;top:50px}
.header-social span:nth-child(1){background:#3b5998}
.header-social span:nth-child(2){background:#1da1f2}
.header-social span:nth-child(3){background:#0077b5}
.header-social span:nth-child(4){background:#dd4b39}
.login{position:absolute;left:1022px;top:45px;width:88px;height:32px;border:1.5px solid var(--orange);border-radius:16px;color:var(--orange);font-size:13px;text-align:center;line-height:29px;letter-spacing:1px}
.main-nav{position:absolute;top:110px;font-family:'Nunito',sans-serif;font-size:16px;color:var(--ink);letter-spacing:.5px;white-space:nowrap}

/* hero */
.hero{position:absolute;left:0;top:165px;width:1200px;height:562px}
.hero-photo{position:absolute;inset:0;background:linear-gradient(110deg,#5c5e63 0%,#8b8680 35%,#a9a6a2 55%,#6d6c6a 80%,#3e3f44 100%)}
.hero-title{position:absolute;left:0;width:1200px;top:245px;text-align:center;font-family:'Nunito',sans-serif;color:var(--white);font-size:60px;font-weight:400;letter-spacing:1px;line-height:1}
.hero-sub{position:absolute;left:0;width:1200px;top:325px;text-align:center;font-family:'Nunito',sans-serif;color:var(--white);font-size:30px;font-weight:600}
.slider-arrow{position:absolute;top:281px;width:26px;height:26px;border-radius:50%;background:rgba(0,0,0,.55);display:flex;align-items:center;justify-content:center}

/* about */
.about{position:absolute;left:0;top:727px;width:1200px;height:559px;background:var(--white)}
.about-photo{position:absolute;left:96px;top:178px;width:364px;height:364px;border-radius:50%;border:8px solid var(--orange);background:radial-gradient(circle at 50% 70%,#e4c4ac 0%,#b6b8bf 55%,#6f8aa3 100%)}
.section-mark{position:absolute;left:524px;top:135px;width:40px;height:40px;border-radius:50%;background:var(--orange)}
.about-title{position:absolute;left:578px;top:125px;font-family:'Nunito',sans-serif;font-size:38px;color:var(--ink);font-weight:400;line-height:1.2}
.about-lead{position:absolute;left:578px;top:172px;font-family:'Nunito',sans-serif;font-size:19px;color:var(--ink)}
.about-text{position:absolute;left:518px;top:212px;width:575px;font-size:14px;line-height:23px;color:var(--text);text-align:justify}
.btn{position:absolute;background:var(--orange);color:var(--white);border-radius:20px;text-align:center;font-size:15px}
.about .btn{left:513px;top:396px;width:127px;height:38px;line-height:38px}

/* services */
.services{position:absolute;left:0;top:1286px;width:1200px;height:511px}
.services-bg{position:absolute;inset:0;background:linear-gradient(90deg,#141414 0%,#2b2826 40%,#242220 70%,#121212 100%)}
.section-title{position:absolute;left:0;width:1200px;text-align:center;font-family:'Nunito',sans-serif;font-weight:600;color:var(--ink)}
.services .section-title{top:76px;font-size:34px;color:var(--white)}
.service{position:absolute;top:175px;width:320px;text-align:center;color:var(--white)}
.service-icon{width:106px;height:106px;margin:0 auto;border-radius:50%;background:var(--orange);display:flex;align-items:center;justify-content:center}
.service h3{font-family:'Nunito',sans-serif;font-weight:400;font-size:22px;margin-top:16px}
.service p{font-size:13.5px;line-height:22px;margin-top:6px}
.service .more{font-size:13.5px;margin-top:4px;display:block}

/* events */
.events{position:absolute;left:0;top:1797px;width:1200px;height:642px;background:var(--white)}
.events .section-title{top:98px;font-size:36px;font-weight:400}
.section-intro{position:absolute;left:0;width:1200px;top:160px;text-align:center;font-size:14px;color:var(--ink)}
.event{position:absolute;top:244px;width:312px}
.event-photo{height:171px}
.event-meta{display:flex;margin-top:13px;height:22px;font-size:12px;line-height:22px}
.event-date{background:var(--orange);color:var(--white);width:72px;padding-left:12px}
.event-comments{background:var(--ink);color:var(--white);width:40px;display:flex;align-items:center;justify-content:center;gap:3px}
.event h3{font-family:'Open Sans',sans-serif;font-weight:600;font-size:16px;color:var(--ink);margin-top:16px}
.event p{font-size:13px;line-height:20px;color:var(--text);margin-top:6px}
.link-orange{color:var(--orange);font-size:13px;display:block;margin-top:4px}

/* blog */
.blog{position:absolute;left:0;top:2439px;width:1200px;height:432px;background:var(--light)}
.blog .section-title{top:76px;font-size:30px;font-weight:400}
.post{position:absolute;top:160px;width:498px;height:169px;background:var(--white);box-shadow:0 2px 6px rgba(0,0,0,.15);display:flex}
.post-photo{width:163px;height:169px;flex:none}
.post-body{padding:22px 20px 0 26px}
.post h3{font-weight:400;font-size:15px;color:var(--ink)}
.post time{display:block;font-size:12px;color:var(--ink);margin-top:6px}
.post p{font-size:11.5px;line-height:19px;color:var(--text);margin-top:4px}
.post .link-orange{font-size:12px;margin-top:2px}

/* footer */
.site-footer{position:absolute;left:0;top:2871px;width:1200px;height:338px;background:var(--footer);color:#cfcfcf}
.footer-brand{position:absolute;left:76px;top:150px;width:220px;text-align:center;white-space:nowrap;font-family:'Nunito',sans-serif;font-weight:700;font-size:24px;color:var(--white);line-height:1}
.footer-brand-sub{position:absolute;left:76px;top:180px;width:220px;text-align:center;white-space:nowrap;font-family:'Nunito',sans-serif;font-size:9px;letter-spacing:3px;color:var(--white);line-height:1}
.footer-dot{position:absolute;left:163px;top:84px;width:46px;height:46px;border-radius:50%;background:var(--white)}
.footer-heading{position:absolute;top:70px;font-size:15px;font-weight:400;color:var(--white);letter-spacing:.5px;white-space:nowrap}
.contact-list{position:absolute;left:368px;top:112px;list-style:none;font-size:12px;line-height:22px}
.contact-list li{display:flex;gap:14px;margin-bottom:10px}
.contact-list svg{flex:none;margin-top:4px}
.quick-links{position:absolute;left:700px;top:112px;list-style:none;font-size:12px;line-height:23px}
.quick-links li::before{content:"» ";color:var(--white)}
.mail-note{position:absolute;left:905px;top:110px;width:200px;font-size:11.5px;line-height:19px}
.mail-form{position:absolute;left:905px;top:150px;display:flex}
.mail-input{width:148px;height:30px;background:var(--white);color:#999;font-size:11px;line-height:30px;padding-left:8px}
.mail-submit{width:56px;height:30px;background:var(--orange);color:var(--white);font-size:12px;line-height:30px;text-align:center}
.footer-rule{position:absolute;left:88px;top:263px;width:1024px;height:1px;background:#444}
.copyright{position:absolute;left:88px;top:290px;font-size:12px}
.footer-social{right:98px;top:286px;gap:12px}
.footer-social span{background:var(--white)}
</style>
</head>
<body>

<header class="site-header">
  <span class="brand-dot"></span>
  <div class="brand">Marlowe Finch</div>
  <div class="brand-sub">PERSONAL TRAINING</div>

  <div class="header-phone">
    <svg width="18" height="18" viewBox="0 0 24 24"><rect width="24" height="24" rx="4" fill="#f7941d"/><path d="M7 5l3 0 1 4-2 1a9 9 0 0 0 5 5l1-2 4 1v3a2 2 0 0 1-2 2C11 19 5 13 5 7a2 2 0 0 1 2-2z" fill="#fff"/></svg>
    555/014-2290
  </div>
  <div class="social header-social"><span></span><span></span><span></span><span></span></div>
  <a class="login" href="#">LOGIN</a>

  <nav>
    <a class="main-nav" style="left:460px" href="#">HOME</a>
    <a class="main-nav" style="left:554px" href="#about">ABOUT ME</a>
    <a class="main-nav" style="left:684px" href="#services">MY SERVICES</a>
    <a class="main-nav" style="left:832px" href="#events">EVENTS</a>
    <a class="main-nav" style="left:941px" href="#blog">BLOG</a>
    <a class="main-nav" style="left:1037px" href="#contact">CONTACT</a>
  </nav>
</header>

<section class="hero">
  <div class="hero-photo" role="img" aria-label="Woman training with suspension straps in a gym"></div>
  <h1 class="hero-title">MARLOWE FINCH</h1>
  <p class="hero-sub">PERSONAL TRAINING</p>
  <span class="slider-arrow" style="left:70px"><svg width="10" height="10" viewBox="0 0 10 10"><path d="M7 1L3 5l4 4" stroke="#fff" stroke-width="2" fill="none"/></svg></span>
  <span class="slider-arrow" style="left:1100px"><svg width="10" height="10" viewBox="0 0 10 10"><path d="M3 1l4 4-4 4" stroke="#fff" stroke-width="2" fill="none"/></svg></span>
</section>

<section class="about" id="about">
  <div class="about-photo" role="img" aria-label="Portrait of the trainer at the beach"></div>
  <span class="section-mark"></span>
  <h2 class="about-title">ABOUT ME</h2>
  <p class="about-lead">Neque porro quisquam est qui dolorem</p>
  <p class="about-text">It is a long established fact that a reader will be distracted by the readable content of a page when looking at its layout. The point of using Lorem Ipsum is that it has a more-or-less normal distribution of letters, as opposed to using 'Content here, content here', making it look like readable English. Many desktop publishing packages and web page editors now use Lorem Ipsum as their default model text, and a search for 'lorem ipsum' will uncover many web sites still in their infancy. Various versions have evolved over the years, sometimes by accident, sometimes on purpose</p>
  <a class="btn" href="#">Read More</a>
</section>

<section class="services" id="services">
  <div class="services-bg" role="img" aria-label="Group fitness class in a dim studio"></div>
  <h2 class="section-title">MY SERVICES</h2>

  <div class="service" style="left:118px">
    <div class="service-icon"><svg width="54" height="54" viewBox="0 0 54 54" fill="#fff"><rect x="6" y="23" width="6" height="8"/><rect x="12" y="17" width="6" height="20"/><rect x="18" y="25" width="18" height="4"/><rect x="36" y="17" width="6" height="20"/><rect x="42" y="23" width="6" height="8"/></svg></div>
    <h3>Quisquam</h3>
    <p>It is a long established fact that a reader<br>will be distracted by the readable</p>
    <a class="more" href="#">Learn More -&gt;</a>
  </div>
  <div class="service" style="left:439px">
    <div class="service-icon"><svg width="54" height="54" viewBox="0 0 54 54"><circle cx="27" cy="29" r="16" stroke="#fff" stroke-width="4" fill="none"/><rect x="23" y="6" width="8" height="5" fill="#fff"/><path d="M27 29V19" stroke="#fff" stroke-width="4"/></svg></div>
    <h3>Dolorem</h3>
    <p>It is a long established fact that a reader<br>will be distracted by the readable</p>
    <a class="more" href="#">Learn More -&gt;</a>
  </div>
  <div class="service" style="left:756px">
    <div class="service-icon"><svg width="54" height="54" viewBox="0 0 54 54"><path d="M27 44L10 27a9 9 0 0 1 17-10 9 9 0 0 1 17 10z" fill="#fff"/></svg></div>
    <h3>Porro quisquam</h3>
    <p>It is a long established fact that a reader<br>will be distracted by the readable content</p>
    <a class="more" href="#">Learn More -&gt;</a>
  </div>
</section>

<section class="events" id="events">
  <h2 class="section-title">EVENTS</h2>
  <p class="section-intro">It has survived not only five centuries, but also the leap into electronic typesetting.</p>

  <article class="event" style="left:96px">
    <div class="event-photo" role="img" aria-label="Woman stretching on an exercise ball" style="background:linear-gradient(120deg,#cdd9e0,#9fb4c2 60%,#7f8d98)"></div>
    <div class="event-meta"><span class="event-date">Dec 03</span><span class="event-comments"><svg width="12" height="10" viewBox="0 0 12 10"><path d="M1 1h10v6H5L2 9V7H1z" fill="none" stroke="#fff"/></svg>0</span></div>
    <h3>Neque porro quisquam dolorem</h3>
    <p>It has survived not only five centuries, but also the leap into electronic typesetting.</p>
    <a class="link-orange" href="#">View More &gt;</a>
  </article>
  <article class="event" style="left:445px">
    <div class="event-photo" role="img" aria-label="Group lunging in a bright loft studio" style="background:linear-gradient(120deg,#4a3d33,#a38a6e 50%,#3b3029)"></div>
    <div class="event-meta"><span class="event-date">Dec 03</span><span class="event-comments"><svg width="12" height="10" viewBox="0 0 12 10"><path d="M1 1h10v6H5L2 9V7H1z" fill="none" stroke="#fff"/></svg>0</span></div>
    <h3>Porro quisquam est qui</h3>
    <p>It has survived not only five centuries, but also the leap into electronic typesetting.</p>
    <a class="link-orange" href="#">View&nbsp; More &gt;</a>
  </article>
  <article class="event" style="left:798px">
    <div class="event-photo" role="img" aria-label="Women doing side planks on mats" style="background:linear-gradient(120deg,#8a5a3c,#c9967a 50%,#6e4a36)"></div>
    <div class="event-meta"><span class="event-date">Dec 03</span><span class="event-comments"><svg width="12" height="10" viewBox="0 0 12 10"><path d="M1 1h10v6H5L2 9V7H1z" fill="none" stroke="#fff"/></svg>0</span></div>
    <h3>Dolorem ipsum quia dolor</h3>
    <p>It has survived not only five centuries, but also the leap into electronic typesetting.</p>
    <a class="link-orange" href="#">View More &gt;</a>
  </article>
</section>

<section class="blog" id="blog">
  <h2 class="section-title">LATEST BLOG</h2>

  <article class="post" style="left:88px">
    <div class="post-photo" role="img" aria-label="Trainer coaching a client with weights" style="background:linear-gradient(135deg,#6b6f73,#a69b91 55%,#4d4f52)"></div>
    <div class="post-body">
      <h3>Nemo Enim Ipsam Volup</h3>
      <time>09-07-2017</time>
      <p>Lorem Ipsum has been the industry's standard dummy text ever since the 1500s, when an unknown printer took a galley of type and scrambled it to make</p>
      <a class="link-orange" href="#">Read More &gt;&gt;</a>
    </div>
  </article>
  <article class="post" style="left:614px">
    <div class="post-photo" role="img" aria-label="Women sitting cross-legged in a yoga class" style="background:linear-gradient(135deg,#d9c7b5,#c5a48c 55%,#9a8574)"></div>
    <div class="post-body">
      <h3>Nemo Enim Ipsam Volup</h3>
      <time>09-07-2017</time>
      <p>Lorem Ipsum has been the industry's standard dummy text ever since the 1500s, when an unknown printer took a galley of type and scrambled it to make</p>
      <a class="link-orange" href="#">Read More &gt;&gt;</a>
    </div>
  </article>
</section>

<footer class="site-footer" id="contact">
  <span class="footer-dot"></span>
  <div class="footer-brand">Marlowe Finch</div>
  <div class="footer-brand-sub">PERSONAL TRAINING</div>

  <h4 class="footer-heading" style="left:368px">CONTACT US</h4>
  <ul class="contact-list">
    <li><svg width="12" height="14" viewBox="0 0 12 14"><path d="M6 0a5 5 0 0 1 5 5c0 4-5 9-5 9S1 9 1 5a5 5 0 0 1 5-5z" fill="#fff"/><circle cx="6" cy="5" r="2" fill="#2a2a2a"/></svg><span>42 Harrow Lane, Suite 8<br>Camden, London</span></li>
    <li><svg width="12" height="12" viewBox="0 0 24 24"><path d="M5 2l4 0 2 6-3 2a12 12 0 0 0 6 6l2-3 6 2v4a2 2 0 0 1-2 2C10 21 3 14 3 4a2 2 0 0 1 2-2z" fill="#fff"/></svg><span>020.7946.0321</span></li>
    <li><svg width="13" height="10" viewBox="0 0 13 10"><rect width="13" height="10" fill="#fff"/><path d="M0 0l6.5 5L13 0" stroke="#2a2a2a" fill="none"/></svg><span>hello@marlowefinch.com</span></li>
  </ul>

  <h4 class="footer-heading" style="left:697px">QUICK LINKS</h4>
  <ul class="quick-links">
    <li>About us</li><li>My Services</li><li>Events</li><li>Blog</li>
  </ul>

  <h4 class="footer-heading" style="left:905px">JOIN OUR MAILING LIST</h4>
  <p class="mail-note">Your about us information would fit here nicely.</p>
  <div class="mail-form"><span class="mail-input">Email address</span><span class="mail-submit">Submit</span></div>

  <div class="footer-rule"></div>
  <p class="copyright">Copyright © 2017. All Rights Reserved</p>
  <div class="social footer-social"><span></span><span></span><span></span><span></span></div>
</footer>

</body>
</html>
```